UI/ UX Design for ERP Software

We need a new UX/UI interface for a ERP software for property managers. Our CMMS / ERP solution is made based on responsive design technologies and is coded in PHP.
The overall UX to be similar to Tev Ulna - easy navigation, intuitive menus.

Industry/Entity Type

Property Management

Number of Pages Required

5+ page

Requirements
Must have
• Round dock buttons
Consistent icons across the application
Enough Spacing between buttons/icons/ menu
Consistent Font
Nice to have
• We would like the UX to allow the users to use the application without /minimum training.
Should not have
• we don't want anything that is classic with respect to UX

```html
<!DOCTYPE html>
<html lang="en">
<head>
<meta charset="utf-8">
<title>Lotwise · Properties list</title>
<link href="https://fonts.googleapis.com/css2?family=Inter:wght@400;500;600;700&display=swap" rel="stylesheet">
<style>
  :root{
    --page:#f6fafc;
    --window:#ffffff;
    --ink:#17202b;
    --muted:#5b7895;
    --primary:#0d8bf2;
    --primary-deep:#0b6fe0;
    --band:#e3eef8;
    --soft-blue:#cfe4fb;
    --cyan:#10b2f2;
    --cyan-soft:#a8e6fd;
    --coral:#f2703f;
    --coral-soft:#f6d0c2;
    --orange:#f7792d;
    --line:#e2e8ee;
    --chip:#f1f6fb;
    --dark:#142231;
  }
  *{box-sizing:border-box;margin:0;padding:0}
  html,body{width:1200px;height:1200px;overflow:hidden}
  body{background:var(--page);font-family:"Inter",sans-serif;color:var(--ink);position:relative}
  .window{position:absolute;left:141px;top:181px;width:918px;height:838px;background:var(--window);border-radius:26px;box-shadow:0 20px 60px rgba(40,80,120,.08)}
  .abs{position:absolute}
  .dot{position:absolute;top:5px;width:7px;height:7px;border-radius:50%}
  .brand{left:29px;top:36px;display:flex;align-items:center;gap:5px;font-weight:600;font-size:15px;color:var(--primary)}
  .brand-mark{width:13px;height:13px;background:var(--primary);border-radius:2px}
  .refresh{left:115px;top:34px;width:109px;height:27px;border-radius:6px;background:#fff;box-shadow:0 3px 12px rgba(30,60,100,.1);display:flex;align-items:center;justify-content:center;gap:5px;font-size:8px;font-weight:500;color:#1b3350}
  .crumbs{left:241px;top:40px;font-size:10px;color:var(--ink)}
  .crumbs b{font-weight:600}
  .welcome{right:77px;top:40px;font-size:10px}
  .welcome b{font-weight:600}
  .avatar{right:29px;top:29px;width:34px;height:34px;border-radius:50%;background:linear-gradient(135deg,#6b5646,#2d3a48)}
  .title-row{left:33px;top:78px;display:flex;align-items:center;gap:9px}
  .back{width:15px;height:15px;border-radius:50%;background:var(--dark);display:flex;align-items:center;justify-content:center}
  .page-title{font-size:16px;font-weight:500;margin-left:2px}
  .props{left:33px;top:115px;display:flex;gap:5px}
  .prop-tab{width:95px;height:29px;border:1px solid var(--line);border-radius:4px;font-size:8px;font-weight:500;display:flex;align-items:center;justify-content:center;background:#fff}
  .seg{top:161px;height:41px;border-radius:4px;display:flex;align-items:center;justify-content:center;gap:6px;font-size:9.5px;font-weight:600}
  .seg.active{left:34px;width:142px;background:var(--primary);color:#fff;box-shadow:0 6px 14px rgba(13,139,242,.25)}
  .seg.idle{left:186px;width:160px;background:var(--chip);color:var(--ink);font-weight:500}
  .card{position:absolute;background:#fff;border-radius:10px;box-shadow:0 4px 18px rgba(40,80,120,.07)}
  .stat-title{position:absolute;top:17px;left:0;right:0;text-align:center;font-size:7.6px;font-weight:600;line-height:1.5}
  .pie{position:absolute;left:34px;top:44px}
  .legend{position:absolute;left:10px;top:108px;font-size:7.4px;line-height:13px}
  .legend li{list-style:none;display:flex;align-items:center;gap:7px}
  .legend .muted{color:var(--muted)}
  .legend i{width:5px;height:5px;border-radius:50%;display:inline-block}
  .table-card{left:170px;width:589px;height:120px}
  .table-card h2{position:absolute;left:13px;top:9px;font-size:12.5px;font-weight:500}
  .grid{position:absolute;left:10px;right:13px;display:grid;grid-template-columns:84px 156px 97px 112px 1fr;padding-left:12px}
  .grid.head{top:29px;height:24px;background:var(--band);border-radius:3px;align-items:center;font-size:10px;font-weight:500}
  .grid.row{font-size:9.4px;color:var(--muted);height:12px;align-items:center}
  .grid.r1{top:60px}.grid.r2{top:82px}
  .tip{position:absolute;left:31px;top:56px;width:51px;height:19px;background:var(--dark);border-radius:3px;color:#fff;font-size:6.5px;font-weight:700;display:flex;align-items:center;justify-content:center}
  .tip:after{content:"";position:absolute;bottom:-4px;left:24px;border:4px solid transparent;border-bottom:0;border-top-color:var(--dark)}
  .dock{left:386px;top:756px;width:146px;height:58px;border-radius:12px;background:#fff;box-shadow:0 6px 22px rgba(40,80,120,.08)}
  .dock-btn{position:absolute;top:9px;width:38px;height:38px;border-radius:10px;display:flex;align-items:center;justify-content:center}
  .dock-btn.home{left:21px;background:linear-gradient(180deg,#1aa2ff,#0a78e8)}
  .dock-btn.apps{left:90px;background:linear-gradient(180deg,#fb8a3a,#f3651f)}
</style>
</head>
<body>
<main class="window">
  <span class="dot" style="left:29px;top:5px;background:#fbcf3c"></span>
  <span class="dot" style="left:42px;background:#f4494a"></span>
  <span class="dot" style="left:55px;background:#3fdc8a"></span>

  <header>
    <div class="abs brand"><span class="brand-mark"></span>Lotwise</div>
    <button class="abs refresh" style="border:0">
      <svg width="9" height="9" viewBox="0 0 12 12" fill="none" stroke="#1b3350" stroke-width="1.6"><path d="M10 6a4 4 0 1 1-2-3.5"/><path d="M8 1v2.5h2.5"/></svg>
      Refresh this page
    </button>
    <nav class="abs crumbs"><b>Home</b> &nbsp;/&nbsp; Properties</nav>
    <div class="abs welcome">Welcome, <b>Arlo Penrick</b></div>
    <div class="abs avatar" role="img" aria-label="Profile photo of the signed-in user"></div>
  </header>

  <div class="abs title-row">
    <span class="back"><svg width="7" height="7" viewBox="0 0 8 8"><path d="M5 1 2 4l3 3" stroke="#fff" stroke-width="1.5" fill="none"/></svg></span>
    <svg width="18" height="17" viewBox="0 0 18 17" fill="none" stroke="#17202b" stroke-width="1.2"><rect x="1.5" y="1.5" width="8" height="15"/><rect x="9.5" y="6.5" width="7" height="10"/><path d="M3.5 4h4M3.5 7h4M3.5 10h4M11.5 9.5h3M11.5 12h3M4.5 13v3.5"/></svg>
    <h1 class="page-title">Properties list</h1>
  </div>

  <div class="abs props">
    <div class="prop-tab">Cedar court</div><div class="prop-tab">Cedar court</div><div class="prop-tab">Cedar court</div><div class="prop-tab">Cedar court</div><div class="prop-tab">Cedar court</div><div class="prop-tab">Cedar court</div><div class="prop-tab">Cedar court</div>
  </div>

  <div class="abs seg active">
    <svg width="12" height="12" viewBox="0 0 12 12" fill="none" stroke="#fff" stroke-width="1.2"><rect x="1.5" y="2" width="9" height="9.5" rx="1.5"/><path d="M4 1v2h4V1"/></svg>
    Request / orders
  </div>
  <div class="abs seg idle">
    <svg width="11" height="11" viewBox="0 0 12 12" fill="none" stroke="#17202b" stroke-width="1.1"><rect x="1" y="2" width="10" height="9" rx="1"/><path d="M1 5h10M4 1v2M8 1v2"/></svg>
    Maintenance calendar
  </div>

  <!-- left stats -->
  <section class="card" style="left:33px;top:222px;width:123px;height:142px">
    <h3 class="stat-title">Tenant request by user</h3>
    <svg class="pie" width="54" height="54" viewBox="0 0 54 54"><circle cx="27" cy="27" r="27" fill="var(--soft-blue)"/><path d="M27 27 27 0A27 27 0 0 1 44.4 47.7Z" fill="var(--primary-deep)"/></svg>
    <ul class="legend"><li class="muted"><i style="background:var(--soft-blue)"></i>No complete (100)</li><li><i style="background:var(--primary-deep)"></i>Completed (65)</li></ul>
  </section>
  <section class="card" style="left:33px;top:380px;width:123px;height:143px">
    <h3 class="stat-title">Maintenance by user</h3>
    <svg class="pie" width="54" height="54" viewBox="0 0 54 54"><circle cx="27" cy="27" r="27" fill="var(--coral-soft)"/><path d="M27 27 27 0A27 27 0 0 1 44.4 47.7Z" fill="var(--coral)"/></svg>
    <ul class="legend"><li class="muted"><i style="background:var(--soft-blue)"></i>No complete (100)</li><li><i style="background:var(--coral)"></i>Completed (65)</li></ul>
  </section>

  <!-- tables -->
  <section class="card table-card" style="top:222px">
    <h2>Tenant request</h2>
    <div class="grid head"><span>Ticket ID</span><span>Subject</span><span>Date</span><span>Property</span><span>Tenant</span></div>
    <div class="grid row r1"><span>1232132323</span><span>Request for rent freeze</span><span>01/01/2021</span><span>Cedar court</span><span>Mira Halden</span></div>
    <div class="grid row r2"><span>1232132323</span><span>Bad neighboors</span><span>01/01/2021</span><span>Cedar court</span><span>Mira Halden</span></div>
  </section>
  <section class="card table-card" style="top:355px">
    <h2>Maintenance</h2>
    <div class="grid head"><span>Ticket ID</span><span>Subject</span><span>Date</span><span>Property</span><span>Tenant</span></div>
    <div class="grid row r1"><span>1232132323</span><span>Request for rent freeze</span><span>01/01/2021</span><span>Cedar court</span><span>Mira Halden</span></div>
    <div class="grid row r2"><span>1232132323</span><span>Bad neighboors</span><span>01/01/2021</span><span>Cedar court</span><span>Mira Halden</span></div>
  </section>
  <section class="card table-card" style="top:484px">
    <h2>Work orders</h2>
    <div class="grid head"><span>Ticket ID</span><span>Subject</span><span>Date</span><span>Property</span><span>Tenant</span></div>
    <div class="grid row r1"><span>1232132323</span><span>Request for rent freeze</span><span>01/01/2021</span><span>Cedar court</span><span>Mira Halden</span></div>
    <div class="grid row r2"><span>1232132323</span><span>Bad neighboors</span><span>01/01/2021</span><span>Cedar court</span><span>Mira Halden</span></div>
  </section>
  <section class="card table-card" style="top:612px">
    <h2>Purcharse orders</h2>
    <div class="grid head"><span>Ticket ID</span><span>Subject</span><span>Date</span><span>Property</span><span>Tenant</span></div>
    <div class="grid row r1"><span>1232132323</span><span>Request for rent freeze</span><span>01/01/2021</span><span>Cedar court</span><span>Mira Halden</span></div>
    <div class="grid row r2"><span>1232132323</span><span>Bad neighboors</span><span>01/01/2021</span><span>Cedar court</span><span>Mira Halden</span></div>
  </section>

  <!-- right stats -->
  <section class="card" style="left:772px;top:222px;width:122px;height:142px">
    <h3 class="stat-title">Montly maintenance</h3>
    <svg class="pie" width="54" height="54" viewBox="0 0 54 54"><circle cx="27" cy="27" r="27" fill="var(--cyan-soft)"/><path d="M27 27 27 0A27 27 0 0 1 44.4 47.7Z" fill="var(--cyan)"/></svg>
    <ul class="legend"><li class="muted"><i style="background:var(--cyan-soft)"></i>No complete (100)</li><li><i style="background:var(--cyan)"></i>Completed (65)</li></ul>
  </section>
  <section class="card" style="left:772px;top:380px;width:122px;height:136px">
    <h3 class="stat-title">Purcharse orders<br>this week</h3>
    <div class="tip">8 orders</div>
    <svg class="abs" style="left:0;top:0" width="122" height="136" viewBox="0 0 122 136">
      <path d="M7 120 27 96 37 104 47 91 54 102 58 94 85 78 114 120Z" fill="var(--cyan)"/>
      <circle cx="58" cy="94" r="5" fill="#7fd6fb" opacity=".7"/>
      <circle cx="58" cy="94" r="3" fill="#3ec2f7"/>
    </svg>
  </section>

  <nav class="abs dock">
    <div class="dock-btn home"><svg width="16" height="15" viewBox="0 0 16 15"><path d="M8 1 1 7.5h2V14h4v-4h2v4h4V7.5h2Z" fill="#fff"/></svg></div>
    <div class="dock-btn apps"><svg width="16" height="16" viewBox="0 0 16 16" fill="#fff"><circle cx="2.5" cy="2.5" r="1.5"/><circle cx="8" cy="2.5" r="1.5"/><circle cx="13.5" cy="2.5" r="1.5"/><circle cx="2.5" cy="8" r="1.5"/><circle cx="8" cy="8" r="1.5"/><circle cx="13.5" cy="8" r="1.5"/><circle cx="2.5" cy="13.5" r="1.5"/><circle cx="8" cy="13.5" r="1.5"/><circle cx="13.5" cy="13.5" r="1.5"/></svg></div>
  </nav>
</main>
</body>
</html>
```